Merrow Trade finance web design

We are a newly established business which provides invoice finance to Small Businesses in England and Wales.
Our approach is very much a funder where the small business owner can talk to the decision maker. We will guarantee on receipt of information, a decision within 24 hours.
We are not a bank so the look of the website need to be friendly but professional.
Have two types of people we are trying to attract to the website: 1) partners who are small business owners and 2) introducers who is accountants and commercial brokers who introduce us to the small businesses.
Currently no website, although domain has been reserved.
The design should be:
Professional
“Clean” Look
Designed to convey Trust and Authority.
Appeal to the small business owner.
Must incorporate:
Logo (attached)
Front page:Top tabs to other pages 1) About us 2) Services 3) Introducers 4) Contact us
Need picture and logo on page.
1) About us page- Room for talk about the company, the people and our critera.
2) Services page- We need for what invoice finance is, and 5 boxes for different services we will provide. (link on page to contact us)
3) Introducers page- We need a part for why become an introducer? Who we can help? Why we are different? (link on page to contact us)
4) Contact us page- Office address, email, tel and if possible a map and a contact me part which will email direct to us.
Text will be provided for the design, if we can see the setup of the website we will provide a part for each of the pages to support.
Styles we think convey the correct image:
www.dornelcapital.example
www.plivanlend.example
www.quorbacredit.example
Target Market(s)
Small business owners
Industry/Entity Type
Finance
Number of Pages Required
5+ page
Look and feel

```html
<!DOCTYPE html>
<html lang="en">
<head>
<meta charset="utf-8">
<title>Merrow Trade finance</title>
<link href="https://fonts.googleapis.com/css2?family=Open+Sans:wght@400;600;700&family=Raleway:wght@500;700;800&display=swap" rel="stylesheet">
<style>
:root{
  --navy:#1f2a38;
  --ink:#2c3e50;
  --text:#6d7177;
  --muted:#9aa0a6;
  --orange:#e8740c;
  --orange-dark:#d35400;
  --amber:#f39c12;
  --teal:#1abc9c;
  --light:#f4f4f4;
  --line:#e4e4e4;
  --dark:#2b2b2b;
  --white:#ffffff;
}
*{box-sizing:border-box;margin:0;padding:0}
html,body{width:1200px;height:4390px;overflow:hidden}
body{font-family:"Open Sans",Arial,sans-serif;color:var(--text);background:var(--white);font-size:14px;line-height:1.6}
section,header,footer,.topbar{position:relative;width:1200px;overflow:hidden}
.abs{position:absolute}
h2.section-title{position:absolute;left:91px;font-family:"Raleway",sans-serif;font-weight:800;font-size:22px;letter-spacing:1px;color:var(--ink);text-transform:uppercase}
h2.section-title span{color:var(--orange)}
h2.section-title::after{content:"";position:absolute;left:0;bottom:-12px;width:48px;height:3px;background:var(--orange)}
.btn-outline{position:absolute;display:inline-block;border:1px solid #ccc;padding:8px 20px;font-size:11px;letter-spacing:2px;text-transform:uppercase;color:var(--muted)}
.photo{position:absolute}

/* top bar */
.topbar{height:41px;background:var(--navy);color:#cfd6de;font-size:12px}
.topbar .call{left:91px;top:11px}
.topbar .right{right:91px;top:11px;display:flex;gap:14px;align-items:center}
.dot{width:10px;height:10px;border-radius:50%;background:#cfd6de;display:inline-block}

/* nav */
.nav{height:91px;border-bottom:1px solid var(--line)}
.logo{font-family:"Raleway",sans-serif;font-weight:800;font-size:34px;color:var(--ink);display:flex;align-items:center;gap:8px}
.logo i{width:14px;height:14px;border-radius:50%;background:var(--orange);display:inline-block}
.nav .logo{left:91px;top:22px}
.nav ul{list-style:none;position:absolute;right:91px;top:34px;display:flex;gap:34px;font-size:12px;font-weight:600;letter-spacing:1px;color:var(--ink)}
.nav li.active{color:var(--orange);border-top:2px solid var(--orange);margin-top:-2px}

/* hero */
.hero{height:439px;background:var(--light)}
.hero .photo{left:160px;top:12px;width:177px;height:427px;background:linear-gradient(180deg,#f1ede9,#e2dcd6 60%,#333 100%);border-radius:60px 60px 0 0}
.hero h1{position:absolute;left:448px;top:120px;font-family:"Raleway",sans-serif;font-weight:800;font-size:46px;color:var(--ink);letter-spacing:.5px}
.hero h1 span{color:var(--orange)}
.hero p{position:absolute;left:448px;top:185px;font-size:18px;color:var(--ink)}
.hero .quote{position:absolute;left:448px;top:234px;border:2px solid var(--ink);padding:8px 18px;font-size:14px;color:var(--ink)}

/* about */
.about{height:459px}
.about h2{top:30px}
.about .copy{position:absolute;left:91px;top:115px;width:470px;font-size:12.5px;line-height:1.85}
.about .copy p+p{margin-top:12px}
.about .chart{left:615px;top:80px}
.about .btn-outline{left:91px;top:345px}

/* band */
.band{height:164px;display:flex}
.band div{flex:1;color:var(--white);text-align:center;padding:44px 30px 0}
.band h3{font-family:"Raleway",sans-serif;font-size:12px;font-weight:700;letter-spacing:1px;text-transform:uppercase}
.band p{font-size:12px;margin-top:6px;line-height:1.5}
.band .b1{background:var(--orange)}
.band .b2{background:var(--orange-dark)}
.band .b3{background:var(--amber)}
.band .b4{background:var(--teal)}

/* services */
.services{height:636px;background:#f7f7f7}
.services h2{top:98px}
.card{position:absolute;background:var(--white);box-shadow:0 2px 8px rgba(0,0,0,.12);display:flex}
.card .photo{position:relative;width:249px;flex:none}
.card .body{padding:16px 16px;font-size:12px;line-height:1.7}
.card h3{font-family:"Raleway",sans-serif;font-size:16px;color:var(--ink);font-weight:700;margin-bottom:6px}
.card .more{display:inline-block;margin-top:10px;border:1px solid #ccc;padding:3px 10px;font-size:10px;letter-spacing:1.5px;color:var(--muted)}

/* stats */
.stats{height:228px;background:linear-gradient(90deg,#1c2029,#2a2e38 40%,#3a2f36 70%,#1d2129)}
.stat{position:absolute;top:48px;width:220px;margin-left:-110px;text-align:center;color:var(--white)}
.stat .ico{width:44px;height:44px;border-radius:50%;background:var(--orange);margin:0 auto;display:flex;align-items:center;justify-content:center}
.stat b{display:block;font-family:"Raleway",sans-serif;font-size:32px;font-weight:700;margin-top:12px;line-height:1.2}
.stat span{font-size:13px;font-weight:600}

/* work */
.work{height:600px}
.work h2{top:80px}
.grid{position:absolute;left:91px;top:158px;width:1015px;height:380px;display:grid;grid-template-columns:repeat(4,1fr);grid-template-rows:1fr 1fr}
.grid div{position:relative}
.work .tick{position:absolute;right:0;top:536px;width:30px;height:3px;background:var(--teal)}

/* speciality */
.speciality{height:386px;background:#fafafa}
.speciality h2{top:72px}
.spec-list{position:absolute;list-style:none;font-size:14px;font-weight:600;color:var(--ink)}
.spec-list li{display:flex;align-items:center;gap:14px;height:43px}
.spec-list svg{flex:none}
.speciality .video{left:785px;top:73px;width:321px;height:225px;background:linear-gradient(180deg,#f3f4f1,#dcdcd4 70%,#b9a987)}
.speciality .play{position:absolute;left:135px;top:88px;width:50px;height:50px;border-radius:50%;background:var(--teal);display:flex;align-items:center;justify-content:center}

/* advisors */
.advisors{height:546px}
.advisors h2{top:34px}
.advisor{position:absolute;top:111px;width:234px;height:372px;background:var(--white);box-shadow:0 2px 8px rgba(0,0,0,.12);text-align:center}
.advisor .photo{position:relative;width:100%;height:290px;background:linear-gradient(180deg,#ffffff,#eceef1 50%,#3a4150)}
.advisor h3{font-size:13px;color:var(--ink);font-weight:600;margin-top:20px}
.advisor p{font-size:12px;color:var(--muted)}

/* faq + testimonial */
.faq-wrap{height:464px}
.faq h2{top:70px;left:47px}
.faq-item{position:absolute;left:47px;width:503px;height:44px;border:1px solid #ddd;font-size:12px;font-weight:600;letter-spacing:.5px;color:#555;text-transform:uppercase;padding:0 18px;display:flex;justify-content:space-between;align-items:center}
.faq-wrap .logo{position:absolute;left:47px;top:412px;font-size:30px;line-height:1.2}
.clients{position:absolute;left:600px;top:0;width:600px;height:464px;background:linear-gradient(135deg,#2d3039,#3b3f48)}
.clients h2.section-title{left:40px;top:70px;color:var(--white);font-size:20px}
.clients .who{position:absolute;left:0;width:600px;top:150px;text-align:center}
.clients .who b{display:block;color:var(--amber);font-size:14px;letter-spacing:1px}
.clients .who span{font-size:11px;color:#c9ccd1;letter-spacing:1px}
.clients .avatar{position:absolute;left:120px;top:198px;width:62px;height:62px;border-radius:50%;background:#c7cbd1;border:3px solid var(--white)}
.clients .quote-box{position:absolute;left:50px;top:215px;width:486px;height:147px;background:var(--white);padding:26px 40px 0 130px;font-size:12px;line-height:1.7;text-align:center}
.clients .qmark{position:absolute;right:24px;top:325px;font-family:"Raleway",sans-serif;font-size:72px;font-weight:800;color:var(--teal);line-height:1}
.clients .dots{position:absolute;left:0;width:600px;top:392px;display:flex;gap:8px;justify-content:center}
.clients .dots i{width:8px;height:8px;border-radius:50%;background:#888}
.clients .dots i.on{background:var(--orange)}

/* footer */
.footer{height:336px;background:var(--dark);color:#b8b8b8;font-size:12px;line-height:1.75}
.fcol{position:absolute;top:56px;width:230px}
.fcol h4{font-family:"Raleway",sans-serif;color:var(--amber);font-size:13px;font-weight:800;letter-spacing:1px;text-transform:uppercase;margin-bottom:22px;position:relative}
.fcol h4::after{content:"";position:absolute;left:0;bottom:-8px;width:36px;height:2px;background:var(--orange)}
.post{display:flex;gap:12px;margin-bottom:12px}
.post div{width:74px;height:44px;background:linear-gradient(135deg,#5d6677,#a9b0ba);flex:none}
.fcol ul{list-style:none}
.fcol li{display:flex;gap:10px;align-items:flex-start}
.fcol li svg{flex:none;margin-top:4px}
</style>
</head>
<body>

<div class="topbar">
  <div class="abs call">Call us free for a decision in 24 hours: +44 0113 496 0000</div>
  <div class="abs right"><span class="dot"></span><span class="dot"></span><span class="dot"></span><span class="dot"></span><span class="dot"></span><span>| Login</span><span>| Language ▾</span></div>
</div>

<header class="nav">
  <div class="abs logo">Merrow<i></i></div>
  <ul>
    <li class="active">HOME</li><li>ABOUT US ▾</li><li>SERVICES ▾</li><li>INTRODUCERS ▾</li><li>CONTACT US</li>
    <li><svg width="12" height="12" viewBox="0 0 12 12"><circle cx="5" cy="5" r="3.8" fill="none" stroke="#2c3e50" stroke-width="1.6"/><line x1="8" y1="8" x2="11" y2="11" stroke="#2c3e50" stroke-width="1.8"/></svg></li>
  </ul>
</header>

<section class="hero">
  <div class="photo" role="img" aria-label="Smiling businesswoman in a white shirt with folded arms"></div>
  <h1><span>WE FUND</span> YOUR FUTURE</h1>
  <p>Invoice finance for small businesses, decided within 24 hours.</p>
  <div class="quote">Get a Quote</div>
</section>

<section class="about">
  <h2 class="section-title"><span>About</span></h2>
  <div class="copy">
    <p>Simple invoice finance for small firms across England and Wales. Talk to the person who decides, send your papers and get a clear answer within one working day, with terms set out plainly.</p>
    <p>We are not a bank. We fund growing businesses with a friendly, direct service, work with accountants and brokers who introduce clients, and keep every step open and easy to follow.</p>
  </div>
  <svg class="abs chart" width="483" height="240" viewBox="0 0 483 240" font-family="Open Sans, sans-serif" font-size="10" fill="#888">
    <rect x="170" y="0" width="14" height="8" fill="#f7c8d2" stroke="#e88"/>
    <text x="190" y="8">Funding Growth %</text>
    <g stroke="#e8e8e8">
      <line x1="30" y1="20" x2="483" y2="20"/><line x1="30" y1="44" x2="483" y2="44"/><line x1="30" y1="68" x2="483" y2="68"/><line x1="30" y1="92" x2="483" y2="92"/><line x1="30" y1="116" x2="483" y2="116"/><line x1="30" y1="140" x2="483" y2="140"/><line x1="30" y1="164" x2="483" y2="164"/><line x1="30" y1="188" x2="483" y2="188"/><line x1="30" y1="212" x2="483" y2="212"/>
    </g>
    <g text-anchor="end"><text x="22" y="24">80</text><text x="22" y="48">70</text><text x="22" y="72">60</text><text x="22" y="96">50</text><text x="22" y="120">40</text><text x="22" y="144">30</text><text x="22" y="168">20</text><text x="22" y="192">10</text><text x="22" y="216">0</text></g>
    <rect x="36" y="146" width="34" height="66" fill="#f8d2dc" stroke="#f08aa0"/>
    <rect x="81" y="128" width="34" height="84" fill="#fbe0cc" stroke="#f5a66a"/>
    <rect x="126" y="200" width="34" height="12" fill="#d3ebf8" stroke="#6cb4e4"/>
    <rect x="171" y="167" width="34" height="45" fill="#fdf0cc" stroke="#f4cb5c"/>
    <rect x="216" y="182" width="34" height="30" fill="#fdf0cc" stroke="#f4cb5c"/>
    <rect x="261" y="137" width="34" height="75" fill="#cfeeea" stroke="#5cc7bb"/>
    <rect x="306" y="113" width="34" height="99" fill="#e5d6f6" stroke="#a77fe3"/>
    <rect x="351" y="62" width="34" height="150" fill="#e5d6f6" stroke="#a77fe3"/>
    <rect x="396" y="32" width="34" height="180" fill="#e5d6f6" stroke="#a77fe3"/>
    <rect x="441" y="20" width="34" height="192" fill="#d3ebf8" stroke="#6cb4e4"/>
    <g text-anchor="middle"><text x="53" y="230">2007</text><text x="98" y="230">2008</text><text x="143" y="230">2009</text><text x="188" y="230">2010</text><text x="233" y="230">2011</text><text x="278" y="230">2012</text><text x="323" y="230">2013</text><text x="368" y="230">2014</text><text x="413" y="230">2015</text><text x="458" y="230">2016</text></g>
  </svg>
  <div class="btn-outline">Learn More</div>
</section>

<section class="band">
  <div class="b1"><h3>Invoice Finance</h3><p>Release cash tied up in your unpaid invoices.</p></div>
  <div class="b2"><h3>Cash Flow Planning</h3><p>Clear plans built around your open invoices.</p></div>
  <div class="b3"><h3>Introducers</h3><p>Support for accountants and commercial brokers.</p></div>
  <div class="b4"><h3>Business Advisor</h3><p>Speak directly with the person who makes decisions.</p></div>
</section>

<section class="services">
  <h2 class="section-title">Our <span>Services</span></h2>
  <div class="card" style="left:91px;top:176px;width:495px;height:211px">
    <div class="photo" role="img" aria-label="Team reviewing charts on a desk" style="background:linear-gradient(135deg,#c9d8e6,#7a93ad)"></div>
    <div class="body"><h3>Invoice Discounting</h3>Funding tied to your sales ledger so cash arrives when invoices are raised, not weeks later.<br><span class="more">LEARN MORE</span></div>
  </div>
  <div class="card" style="left:612px;top:176px;width:494px;height:211px">
    <div class="photo" role="img" aria-label="Hand holding a glowing growth chart" style="background:linear-gradient(135deg,#e6edf4,#7fa3c8)"></div>
    <div class="body"><h3>Invoice Factoring</h3>We review your figures with you and set a limit that fits the way your business trades.<br><span class="more">LEARN MORE</span></div>
  </div>
  <div class="card" style="left:91px;top:401px;width:495px;height:147px">
    <div class="photo" role="img" aria-label="Colleagues working together at laptops" style="background:linear-gradient(135deg,#d7c9b8,#6f7f8f)"></div>
    <div class="body">Quick setup with one contact who knows your account and answers your calls.<br><span class="more">LEARN MORE</span></div>
  </div>
  <div class="card" style="left:612px;top:401px;width:494px;height:147px">
    <div class="photo" role="img" aria-label="Advisors meeting around an office table" style="background:linear-gradient(135deg,#ece3d6,#8a7e72)"></div>
    <div class="body">Flexible terms for seasonal trade, new contracts and fast growing orders.<br><span class="more">LEARN MORE</span></div>
  </div>
</section>

<section class="stats" role="img" aria-label="Dimmed office photo behind key figures">
  <div class="stat" style="left:211px"><div class="ico"><svg width="18" height="18" viewBox="0 0 18 18"><rect x="2" y="6" width="14" height="10" fill="#fff"/><rect x="6" y="3" width="6" height="3" fill="none" stroke="#fff" stroke-width="1.5"/></svg></div><b>24</b><span>Hour Decisions</span></div>
  <div class="stat" style="left:445px"><div class="ico"><svg width="18" height="18" viewBox="0 0 18 18"><circle cx="9" cy="6" r="3.5" fill="#fff"/><path d="M2 17c0-4 3-6 7-6s7 2 7 6z" fill="#fff"/></svg></div><b>1442</b><span>Happy Clients</span></div>
  <div class="stat" style="left:732px"><div class="ico"><svg width="18" height="18" viewBox="0 0 18 18"><path d="M9 2l7 13H2z" fill="#fff"/></svg></div><b>4</b><span>Team Advisors</span></div>
  <div class="stat" style="left:989px"><div class="ico"><svg width="18" height="18" viewBox="0 0 18 18"><circle cx="9" cy="9" r="7" fill="none" stroke="#fff" stroke-width="2"/><path d="M9 5v4l3 2" stroke="#fff" stroke-width="2" fill="none"/></svg></div><b>2280</b><span>Invoices Funded</span></div>
</section>

<section class="work">
  <h2 class="section-title"><span>Businesses</span> We Fund</h2>
  <div class="grid">
    <div role="img" aria-label="Hands pointing at a financial report" style="background:linear-gradient(135deg,#dfe8f2,#8fa7c2)"></div>
    <div role="img" aria-label="Laptop on a bright white desk" style="background:linear-gradient(135deg,#f2f2f2,#b8bcc2)"></div>
    <div role="img" aria-label="Coffee and notebook on a sunlit table" style="background:linear-gradient(135deg,#f6d9a8,#9a6c44)"></div>
    <div role="img" aria-label="Tablet with charts on a desk" style="background:linear-gradient(135deg,#e6ebf0,#7c8a98)"></div>
    <div role="img" aria-label="Businessman in a suit" style="background:linear-gradient(135deg,#eeeeee,#3d4654)"></div>
    <div role="img" aria-label="Colourful tablet screen on a keyboard" style="background:linear-gradient(135deg,#e9eef2,#8b97a6)"></div>
    <div role="img" aria-label="Pencil cup on a white desk" style="background:linear-gradient(135deg,#f4f4f4,#9a9a9a)"></div>
    <div role="img" aria-label="Small team talking at a laptop" style="background:linear-gradient(135deg,#d9c7b5,#8a5a4a)"></div>
  </div>
  <div class="tick"></div>
</section>

<section class="speciality">
  <h2 class="section-title">Why <span>Choose Us</span></h2>
  <ul class="spec-list" style="left:94px;top:135px">
    <li><svg width="18" height="18"><circle cx="9" cy="9" r="9" fill="#1abc9c"/><path d="M5 9l3 3 5-6" stroke="#fff" stroke-width="2" fill="none"/></svg>Decision Within 24 Hours</li>
    <li><svg width="18" height="18"><circle cx="9" cy="9" r="9" fill="#1abc9c"/><path d="M5 9l3 3 5-6" stroke="#fff" stroke-width="2" fill="none"/></svg>Friendly Support</li>
    <li><svg width="18" height="18"><circle cx="9" cy="9" r="9" fill="#1abc9c"/><path d="M5 9l3 3 5-6" stroke="#fff" stroke-width="2" fill="none"/></svg>Talk To The Decision Maker</li>
    <li><svg width="18" height="18"><circle cx="9" cy="9" r="9" fill="#1abc9c"/><path d="M5 9l3 3 5-6" stroke="#fff" stroke-width="2" fill="none"/></svg>England And Wales Coverage</li>
  </ul>
  <ul class="spec-list" style="left:439px;top:135px">
    <li><svg width="18" height="18"><circle cx="9" cy="9" r="9" fill="#1abc9c"/><path d="M5 9l3 3 5-6" stroke="#fff" stroke-width="2" fill="none"/></svg>Fast Funding</li>
    <li><svg width="18" height="18"><circle cx="9" cy="9" r="9" fill="#1abc9c"/><path d="M5 9l3 3 5-6" stroke="#fff" stroke-width="2" fill="none"/></svg>Clear, Simple Fees</li>
    <li><svg width="18" height="18"><circle cx="9" cy="9" r="9" fill="#1abc9c"/><path d="M5 9l3 3 5-6" stroke="#fff" stroke-width="2" fill="none"/></svg>Support For Introducers</li>
    <li><svg width="18" height="18"><circle cx="9" cy="9" r="9" fill="#1abc9c"/><path d="M5 9l3 3 5-6" stroke="#fff" stroke-width="2" fill="none"/></svg>No Bank Red Tape</li>
  </ul>
  <div class="photo video" role="img" aria-label="Young plant growing from a pile of coins">
    <div class="play"><svg width="18" height="18"><path d="M5 3l11 6-11 6z" fill="#fff"/></svg></div>
  </div>
</section>

<section class="advisors">
  <h2 class="section-title"><span>Expert</span> Advisors</h2>
  <div class="advisor" style="left:91px"><div class="photo" role="img" aria-label="Portrait of a financial advisor in a suit"></div><h3>Daniel Foster</h3><p>Managing Director</p></div>
  <div class="advisor" style="left:351px"><div class="photo" role="img" aria-label="Portrait of a sales advisor holding a newspaper"></div><h3>Mark Holloway</h3><p>Credit Manager</p></div>
  <div class="advisor" style="left:612px"><div class="photo" role="img" aria-label="Portrait of a tax advisor in a dark suit"></div><h3>Richard Bennett</h3><p>Introducer Manager</p></div>
  <div class="advisor" style="left:872px"><div class="photo" role="img" aria-label="Portrait of a client advisor with a tablet"></div><h3>Thomas Rowe</h3><p>Client Advisor</p></div>
</section>

<section class="faq-wrap">
  <div class="faq">
    <h2 class="section-title"><span>Frequently Asked</span> Questions</h2>
    <div class="faq-item" style="top:160px">How does invoice finance work? <span>▾</span></div>
    <div class="faq-item" style="top:222px">How fast will I get a decision? <span>▾</span></div>
    <div class="faq-item" style="top:284px">Which businesses can you help? <span>▾</span></div>
    <div class="faq-item" style="top:346px">How do I become an introducer? <span>▾</span></div>
    <div class="logo">Merrow<i></i></div>
  </div>
  <div class="clients">
    <h2 class="section-title">What Clients Say</h2>
    <div class="who"><b>JAMES CARTER</b><span>CEO &amp; FOUNDER, NORTHFIELD STUDIO</span></div>
    <div class="quote-box">A decision came back the next day and the team explained every step. Cash flow is steady now and we can take on larger orders with real confidence.</div>
    <div class="avatar" role="img" aria-label="Client portrait"></div>
    <div class="qmark">”</div>
    <div class="dots"><i class="on"></i><i></i><i></i><i></i></div>
  </div>
</section>

<footer class="footer">
  <div class="fcol" style="left:94px;width:220px">
    <h4>About</h4>
    <p>Invoice finance for small firms in England and Wales. Quick answers, plain terms and a real person to talk to whenever you need help with your account.</p>
  </div>
  <div class="fcol" style="left:351px">
    <h4>Latest Post</h4>
    <div class="post"><div role="img" aria-label="Post thumbnail"></div><p>How invoice finance keeps small firms trading</p></div>
    <div class="post"><div role="img" aria-label="Post thumbnail"></div><p>Why accountants refer clients to a direct funder</p></div>
  </div>
  <div class="fcol" style="left:615px">
    <h4>Contact Information</h4>
    <ul>
      <li><svg width="12" height="14"><path d="M6 0a5 5 0 0 1 5 5c0 4-5 9-5 9S1 9 1 5a5 5 0 0 1 5-5z" fill="#e8740c"/><circle cx="6" cy="5" r="2" fill="#2b2b2b"/></svg><span>Unit 12, Carrow Yard,<br>Leeds, United Kingdom</span></li>
      <li><svg width="12" height="12"><rect width="12" height="12" rx="2" fill="#e8740c"/></svg><span>+44 0113 496 0123<br>+44 0113 496 0125</span></li>
      <li><svg width="12" height="10"><rect width="12" height="10" rx="1" fill="#e8740c"/><path d="M0 0l6 5 6-5" stroke="#2b2b2b" fill="none"/></svg><span>info@merrowtrade.example<br>care@merrowtrade.example</span></li>
    </ul>
  </div>
  <div class="fcol" style="left:872px">
    <h4>Useful Links</h4>
    <ul>
      <li>› About us</li><li>› Our Services</li><li>› Become an Introducer</li><li>› Contact us</li><li>› Terms &amp; Conditions</li><li>› Privacy Policy</li>
    </ul>
  </div>
</footer>

</body>
</html>
```